Business Card Design

We are a company that provides stump grinding services for residential and commercial clients. Looking for a simple business card design that may have some type of graphic on the card that will tie in with the Tamsen name(Grizzly Bear, Paw Print, etc) . Possibly some foliage wrapping around part of the card? Would like to have a simple design that stands out because it is unique. We are working on getting the website set up and there is a simple graphic on the top of the page that came to mind when I mentioned the leaves.

Industry/Entity Type

Business

Contact Information for Business Card

Tamsen Stump Grinding 303-257-4788KodiakStumps.Com

Font styles to use
Serif

Requirements
Must have
• Business name
• Website Address
• Phone Number
Nice to have
• Graphics that would be associated with a Tamsen bear.
Should not have
• Nothing frilly

```html
<!DOCTYPE html>
<html lang="en">
<head>
<meta charset="utf-8">
<title>Tamsen Stump Grinding – Business Card</title>
<link rel="stylesheet" href="https://fonts.googleapis.com/css2?family=Lato:wght@400;700&display=swap">
<style>
  :root {
    --page-bg: #3a332f;
    --card-bg: #0b0b0c;
    --brand-blue: #2f8ff0;
    --text-white: #f2f2f2;
    --text-grey: #8a8a8a;
    --mark-white: #ececec;
  }
  * { box-sizing: border-box; margin: 0; padding: 0; }
  html, body {
    width: 1200px;
    height: 900px;
    overflow: hidden;
    background: var(--page-bg);
    font-family: "Lato", sans-serif;
  }
  .sheet {
    position: relative;
    width: 1200px;
    height: 900px;
    display: flex;
    align-items: center;
    justify-content: center;
    gap: 60px;
  }
  .card {
    position: relative;
    width: 520px;
    height: 298px;
    background: var(--card-bg);
    border-radius: 4px;
    box-shadow: 0 10px 30px rgba(0,0,0,0.45);
  }
  .brand {
    position: absolute;
    display: flex;
    align-items: center;
    gap: 14px;
  }
  .brand-dot {
    flex: none;
    border-radius: 50%;
  }
  .brand-name {
    text-transform: uppercase;
    font-weight: 400;
    line-height: 1.15;
  }
  .brand-name .line-main {
    display: block;
    font-size: 27px;
    letter-spacing: 0.5px;
  }
  .brand-name .line-sub {
    display: block;
    font-size: 16px;
    letter-spacing: 16px;
    margin-top: 6px;
  }

  /* front */
  .card-front .brand { left: 48px; top: 70px; }
  .card-front .brand-dot {
    width: 84px; height: 84px;
    background: var(--brand-blue);
    border: 4px solid var(--mark-white);
  }
  .card-front .brand-name { color: var(--brand-blue); }

  .contact {
    position: absolute;
    left: 160px;
    top: 180px;
    list-style: none;
    color: var(--text-white);
    font-size: 16px;
  }
  .contact li {
    display: flex;
    align-items: center;
    gap: 8px;
    margin-bottom: 5px;
  }
  .contact svg { width: 14px; height: 14px; fill: none; stroke: var(--brand-blue); stroke-width: 2; }
  .contact .icon-phone { fill: var(--brand-blue); stroke: none; }

  /* back */
  .card-back .brand { left: 54px; top: 102px; }
  .card-back .brand-dot {
    width: 88px; height: 88px;
    background: var(--mark-white);
  }
  .card-back .brand-name { color: var(--text-grey); }
</style>
</head>
<body>
<main class="sheet">
  <section class="card card-front" aria-label="Business card front">
    <div class="brand">
      <span class="brand-dot"></span>
      <p class="brand-name">
        <span class="line-main">Tamsen Stump</span>
        <span class="line-sub">Grinding</span>
      </p>
    </div>
    <ul class="contact">
      <li>
        <svg class="icon-phone" viewBox="0 0 24 24" aria-hidden="true"><path d="M3 8c0-2 4-4 9-4s9 2 9 4v2h-5V8H8v2H3zM6 12h12l2 8H4z"/></svg>
        <span>303-555-0146</span>
      </li>
      <li>
        <svg viewBox="0 0 24 24" aria-hidden="true"><path d="M10 14a4 4 0 0 0 6 0l3-3a4 4 0 0 0-6-6l-1 1M14 10a4 4 0 0 0-6 0l-3 3a4 4 0 0 0 6 6l1-1"/></svg>
        <span>TamsenStumps.Com</span>
      </li>
    </ul>
  </section>

  <section class="card card-back" aria-label="Business card back">
    <div class="brand">
      <span class="brand-dot"></span>
      <p class="brand-name">
        <span class="line-main">Tamsen Stump</span>
        <span class="line-sub">Grinding</span>
      </p>
    </div>
  </section>
</main>
</body>
</html>
```